Brightway Haul & Upkeep Services, are a company that offers a 'one stop shop' pre-move clean up a

I have already selected a logo which I would like on the front of the business cards along with phone numbers, web address and email which are:
0487650392
www.brightwayhaul.com.au
brightwayhaulandupkeep@mailbox.example

On the back of the card I would like to list some of the types of service we offer (clean - move - repairs/maintenance) which are:
CLEAN - windows, gutters, solar panels, driveways/paths, carpets.
MOVE - Small/medium size house/office moves, large item pick-up & delivery, yard clean-up and removal.
General maintenance and repairs.

I would like the blue logo on a gray background.

Thanks

```html
<!DOCTYPE html>
<html lang="en">
<head>
<meta charset="utf-8">
<title>Brightway Haul &amp; Upkeep Services – Business Card</title>
<link href="https://fonts.googleapis.com/css2?family=PT+Sans:wght@400;700&family=PT+Sans+Narrow:wght@700&display=swap" rel="stylesheet">
<style>
  :root {
    --backdrop: #e6e6e6;
    --card: #ffffff;
    --brand-blue: #1f6db8;
    --ink: #1b1b1b;
    --panel-blue: #cbdaeb;
    --white: #ffffff;
  }
  * { margin: 0; padding: 0; box-sizing: border-box; }
  html, body {
    width: 1200px; height: 375px; overflow: hidden;
    background: var(--backdrop);
  }
  .canvas { position: relative; width: 1200px; height: 375px; }
  .card {
    position: absolute; top: 28px; width: 550px; height: 315px;
    background: var(--card); border-radius: 26px; overflow: hidden;
    font-family: "PT Sans", Arial, sans-serif; color: var(--ink);
    box-shadow: 0 2px 6px rgba(0,0,0,.18);
  }
  .card--front { left: 35px; }
  .card--back { left: 620px; }

  .brand-name {
    position: absolute; left: 0; right: 0; top: 78px;
    text-align: center;
    font-family: "PT Sans Narrow", "Arial Narrow", sans-serif;
    font-weight: 700; font-size: 34px; line-height: 38px;
    text-transform: uppercase; color: var(--brand-blue);
    letter-spacing: .5px;
  }
  .contact {
    position: absolute; left: 0; right: 0; top: 182px;
    text-align: center; padding-left: 45px;
  }
  .contact__line { display: flex; align-items: center; justify-content: center; gap: 6px; }
  .contact__phone { font-size: 19px; line-height: 26px; }
  .contact__email { font-size: 15px; line-height: 24px; margin-top: 2px; }
  .contact__icon { width: 14px; height: 14px; fill: var(--brand-blue); }

  .front-swoosh { position: absolute; left: 0; top: 0; width: 550px; height: 315px; }
  .front-web {
    position: absolute; left: 0; right: 0; bottom: 10px; padding-left: 0;
    text-align: center; color: var(--white); font-size: 15px; letter-spacing: 2.6px;
    transform: translateX(-20px);
  }

  .services-panel {
    position: absolute; left: 25px; top: 123px; width: 502px; height: 114px;
    background: var(--panel-blue); border-radius: 14px; text-align: center;
  }
  .services-panel__title {
    margin-top: 16px; font-weight: 700; font-size: 21px; letter-spacing: 1.6px;
  }
  .services-panel__list { list-style: none; margin-top: 10px; font-weight: 700; font-size: 15px; line-height: 26px; text-transform: uppercase; }
  .back-web {
    position: absolute; left: 0; right: 0; top: 263px;
    text-align: center; font-size: 18px; letter-spacing: 2px;
  }
</style>
</head>
<body>
<main class="canvas">
  <section class="card card--front" aria-label="Card front">
    <svg class="front-swoosh" viewBox="0 0 550 315" aria-hidden="true">
      <path d="M0,226 C150,276 330,286 550,262 L550,315 L0,315 Z" fill="var(--brand-blue)"/>
      <path d="M0,202 C140,250 320,272 462,272 C320,266 150,258 0,222 Z" fill="var(--ink)"/>
    </svg>
    <h1 class="brand-name">Brightway Haul<br>&amp; Upkeep Services</h1>
    <div class="contact">
      <p class="contact__line contact__phone">
        <svg class="contact__icon" viewBox="0 0 24 24" aria-hidden="true"><path d="M6.6 10.8c1.4 2.8 3.8 5.1 6.6 6.6l2.2-2.2c.3-.3.7-.4 1-.2 1.1.4 2.3.6 3.6.6.6 0 1 .4 1 1V20c0 .6-.4 1-1 1C10.6 21 3 13.4 3 4c0-.6.4-1 1-1h3.5c.6 0 1 .4 1 1 0 1.3.2 2.5.6 3.6.1.3 0 .7-.2 1z"/></svg>
        0487650392
      </p>
      <p class="contact__line contact__email">
        <svg class="contact__icon" viewBox="0 0 24 24" aria-hidden="true"><path d="M2 6h20v12H2z M2 6l10 7 10-7" /></svg>
        brightwayhaulandupkeep@mailbox.example
      </p>
    </div>
    <p class="front-web">www.brightwayhaul.com.au</p>
  </section>

  <section class="card card--back" aria-label="Card back">
    <div class="services-panel">
      <h2 class="services-panel__title">Services we offer</h2>
      <ul class="services-panel__list">
        <li>• Clean • Move</li>
        <li>• General maintenance and repairs.</li>
      </ul>
    </div>
    <p class="back-web">www.brightwayhaul.com.au</p>
  </section>
</main>
</body>
</html>
```